Business Card Design for Property Development Company Director

I am looking for a professional and unforgettable business card design for our Director of our Property Development Company.
Please see attached .pptx file to find out what information to include. You don't have to follow the exact format shown in the file - I am interested to see your creative flair using the information provided.

```html
<!DOCTYPE html>
<html lang="en">
<head>
<meta charset="utf-8">
<title>Harwell Property Group – Business Cards</title>
<link href="https://fonts.googleapis.com/css2?family=Roboto:wght@400;700;900&family=Roboto+Condensed:wght@700&display=swap" rel="stylesheet">
<style>
  :root {
    --brand-blue: #26478f;
    --brand-blue-deep: #1f3c7e;
    --swoosh-grey: #5a5c61;
    --ink-grey: #4a4c52;
    --card-white: #f4f4f4;
    --backdrop: #e4e4e4;
    --faint-mark: #e8e8e8;
  }
  * { margin: 0; padding: 0; box-sizing: border-box; }
  html, body { width: 1200px; height: 726px; overflow: hidden; }
  body {
    background: var(--backdrop);
    font-family: "Roboto", Arial, sans-serif;
    position: relative;
  }
  .card {
    position: absolute;
    top: 213px;
    width: 520px;
    height: 300px;
    border-radius: 3px;
    overflow: hidden;
    box-shadow: 0 2px 8px rgba(0,0,0,0.12);
  }
  /* Front */
  .card-front {
    left: 45px;
    background: var(--brand-blue);
    color: #fff;
    text-align: center;
  }
  .tagline {
    margin-top: 34px;
    font-size: 19px;
    line-height: 1.25;
    font-weight: 400;
  }
  .front-brand {
    margin-top: 38px;
    display: flex;
    align-items: center;
    justify-content: center;
    gap: 14px;
  }
  .brand-square {
    width: 54px;
    height: 54px;
    background: #fff;
  }
  .brand-name {
    font-weight: 900;
    text-transform: uppercase;
    text-align: left;
    line-height: 1;
  }
  .front-brand .brand-name { color: #fff; font-size: 46px; letter-spacing: 1px; }
  .brand-name .brand-sub { display: block; font-size: 17px; letter-spacing: 5px; margin-top: 4px; }
  .invite {
    position: absolute;
    left: 0; right: 0; bottom: 34px;
    font-size: 15px;
  }
  /* Back */
  .card-back {
    left: 635px;
    background: var(--card-white);
  }
  .faint-mark {
    position: absolute;
    left: 350px; top: 16px;
    width: 130px; height: 90px;
    background: var(--faint-mark);
  }
  .back-brand {
    position: absolute;
    left: 34px; top: 42px;
    display: flex; align-items: center; gap: 12px;
  }
  .back-brand .brand-square { width: 46px; height: 46px; background: var(--brand-blue); }
  .back-brand .brand-name { color: var(--brand-blue); font-size: 38px; }
  .back-brand .brand-sub { font-size: 14px; letter-spacing: 4px; }
  .contact {
    position: absolute;
    left: 34px; top: 128px;
    color: var(--ink-grey);
    font-size: 14px;
    list-style: none;
    line-height: 1.6;
  }
  .contact .licence { margin-bottom: 4px; }
  .contact .licence span { color: var(--brand-blue); }
  .contact li { display: flex; align-items: center; gap: 9px; }
  .contact svg { width: 12px; height: 12px; fill: var(--ink-grey); flex: none; }
  .waves { position: absolute; inset: 0; }
  .director {
    position: absolute;
    right: 24px; top: 190px;
    text-align: right;
    color: #fff;
  }
  .director .name { font-family: "Roboto Condensed", Arial, sans-serif; font-size: 20px; font-weight: 700; }
  .director .role { font-size: 12px; margin-top: 2px; }
</style>
</head>
<body>

<section class="card card-front">
  <p class="tagline">Property Development<br>&amp; Site Acquisition Specialists</p>
  <div class="front-brand">
    <div class="brand-square"></div>
    <div class="brand-name">Harwell<span class="brand-sub">Property Group</span></div>
  </div>
  <p class="invite">Ask me about our INVESTMENT &amp; PARTNERSHIP opportunities</p>
</section>

<section class="card card-back">
  <div class="faint-mark"></div>
  <svg class="waves" viewBox="0 0 520 300" preserveAspectRatio="none" aria-hidden="true">
    <path fill="var(--swoosh-grey)" d="M150 300 C260 285 310 200 345 155 C375 115 430 98 520 100 L520 114 C440 112 395 125 365 162 C330 210 290 290 205 300 Z"/>
    <path fill="var(--brand-blue-deep)" d="M218 300 C300 290 340 220 370 175 C395 140 440 125 520 128 L520 300 Z"/>
  </svg>
  <div class="back-brand">
    <div class="brand-square"></div>
    <div class="brand-name">Harwell<span class="brand-sub">Property Group</span></div>
  </div>
  <ul class="contact">
    <li class="licence">Real Estate Lic: <span>1234567 &amp; 1234568</span></li>
    <li><svg viewBox="0 0 24 24"><path d="M6.6 10.8a15 15 0 0 0 6.6 6.6l2.2-2.2c.3-.3.7-.4 1-.2 1.1.4 2.3.6 3.6.6.6 0 1 .4 1 1V20c0 .6-.4 1-1 1A17 17 0 0 1 3 4c0-.6.4-1 1-1h3.5c.6 0 1 .4 1 1 0 1.3.2 2.5.6 3.6.1.3 0 .7-.2 1z"/></svg>0400 123 456</li>
    <li><svg viewBox="0 0 24 24"><path d="M2 5h20v14H2z M2 5l10 8 10-8" fill="none" stroke="#4a4c52" stroke-width="2.4"/></svg>daniel@harwell.com.au</li>
    <li><svg viewBox="0 0 24 24"><circle cx="12" cy="12" r="10"/><path d="M2 12h20M12 2c3 3 3 17 0 20M12 2c-3 3-3 17 0 20" stroke="#f4f4f4" stroke-width="1.6" fill="none"/></svg>www.harwell.com.au</li>
  </ul>
  <div class="director">
    <div class="name">Daniel Marsh</div>
    <div class="role">Director</div>
  </div>
</section>

</body>
</html>
```